Launch Website

A very simple, but attractive website (template preferred) is required in a common format - HTML5 or Wordpress etc.
It should be easily user updateable for updates.
Pages it needs:
-Home Page with menu bar, company logo and 1 large graphic/picture and two smaller graphics/logos.
- What we do
- How we do it
- About Us
- Guarantees
- Results
- Contact Page with Enquiry Form
- Provision for a blog to be added later

Most pages will be approx 150 words text with some small/medium images.
We have our own domain & hosting.

A "less is more" design approach would be encouraged.

Target Market(s)

Vehicle Fleet Managers

Industry/Entity Type

It Company

Font styles to use
Sans Serif

Colors
9bcb3c

Requirements
Must have
• Corporate Style. No Fluff.
Nice to have
• Images of LIght Commerical vehicles and trucks

Am ok with white background throughout site.
Colours should match/complement company logo.
Should not have
• Should not be too "busy"

```html
<!DOCTYPE html>
<html lang="en">
<head>
<meta charset="utf-8">
<title>Northway Fleet</title>
<link href="https://fonts.googleapis.com/css2?family=PT+Sans:wght@400;700&family=PT+Sans+Narrow:wght@400;700&family=Arimo:wght@400&display=swap" rel="stylesheet">
<style>
  :root {
    --green: #00a04a;
    --ink: #1e2029;
    --text: #6b6b6b;
    --title: #555555;
    --white: #ffffff;
    --badge-dark: #2a2c30;
    --badge-light: #c9cbcd;
  }
  * { margin: 0; padding: 0; box-sizing: border-box; }
  html, body { width: 1099px; height: 1200px; overflow: hidden; background: var(--white); }
  body { position: relative; font-family: "PT Sans", sans-serif; }

  .site-header { position: absolute; left: 0; top: 0; width: 1099px; height: 109px; }
  .brand { position: absolute; left: 30px; top: 30px; height: 44px; display: flex; align-items: center; gap: 14px; }
  .brand-mark { width: 34px; height: 34px; background: var(--green); }
  .brand-name {
    font-family: "PT Sans", sans-serif; font-weight: 700; font-size: 40px; line-height: 44px;
    color: var(--green); white-space: nowrap;
  }
  .badge-partner { position: absolute; left: 765px; top: 58px; width: 163px; height: 37px; border-radius: 8px; background: var(--badge-dark); }
  .badge-member { position: absolute; left: 952px; top: 36px; width: 115px; height: 52px; border-radius: 4px; background: var(--badge-light); }

  .masthead-band { position: absolute; left: 0; top: 109px; width: 1099px; height: 352px; background: var(--ink); }
  .main-nav { position: absolute; left: 21px; top: 109px; width: 1057px; height: 48px; }
  .main-nav a {
    position: absolute; top: 0; height: 48px; line-height: 48px; color: var(--white);
    text-decoration: none; font-size: 17px; text-transform: uppercase; white-space: nowrap;
    transform: translateX(-50%);
  }
  .main-nav a.is-active { background: var(--green); width: 116px; text-align: center; transform: none; }

  .hero-frame { position: absolute; left: 21px; top: 157px; width: 1057px; height: 435px; background: var(--white); }
  .hero-visual {
    position: absolute; left: 29px; top: 165px; width: 1039px; height: 419px;
    background: linear-gradient(100deg, #f6e27a 0%, #c9b24a 22%, #7f7a4c 40%, #b9b4bf 58%, #d8d3df 75%, #3f5a2c 100%);
  }

  .feature { position: absolute; width: 470px; height: 100px; }
  .feature-icon { position: absolute; left: 0; top: 0; width: 74px; height: 66px; }
  .feature-title { position: absolute; left: 93px; top: 0; font-family: "PT Sans Narrow", sans-serif; font-weight: 700; font-size: 18px; line-height: 22px; color: var(--title); white-space: nowrap; }
  .feature-text { position: absolute; left: 93px; top: 23px; width: 365px; font-family: "PT Sans Narrow", sans-serif; font-size: 13.5px; line-height: 19px; color: var(--text); }

  .site-footer { position: absolute; left: 0; top: 951px; width: 1099px; height: 249px; background: var(--green); color: var(--white); text-align: center; }
  .social-list { position: absolute; left: 0; top: 61px; width: 1099px; height: 49px; }
  .social-link {
    position: absolute; top: 0; width: 49px; height: 49px; border-radius: 50%; background: var(--white);
    color: var(--green); font-family: "PT Sans", sans-serif; font-weight: 700; font-size: 8.5px;
    line-height: 49px; text-align: center; text-decoration: none; transform: translateX(-50%);
  }
  .footer-nav { position: absolute; left: 0; top: 161px; width: 1099px; font-family: "Arimo", sans-serif; font-size: 12.5px; }
  .footer-nav a { color: var(--white); text-decoration: none; }
  .copyright { position: absolute; left: 0; top: 182px; width: 1099px; font-family: "Arimo", sans-serif; font-size: 11px; }
</style>
</head>
<body>
  <header class="site-header">
    <div class="brand">
      <span class="brand-mark" aria-hidden="true"></span>
      <span class="brand-name">Northway Fleet</span>
    </div>
    <div class="badge-partner" aria-hidden="true"></div>
    <div class="badge-member" aria-hidden="true"></div>
  </header>

  <div class="masthead-band"></div>
  <nav class="main-nav">
    <a class="is-active" href="#" style="left:0">Home</a>
    <a href="#" style="left:194px">What We Do</a>
    <a href="#" style="left:366px">How We Do It</a>
    <a href="#" style="left:525px">About Us</a>
    <a href="#" style="left:680px">Guarantees</a>
    <a href="#" style="left:828px">Results</a>
    <a href="#" style="left:974px">Contact Us</a>
  </nav>

  <div class="hero-frame"></div>
  <div class="hero-visual" role="img" aria-label="Articulated truck driving on a country road at sunrise, warm sunlight through trees"></div>

  <section class="feature" style="left:62px;top:664px">
    <svg class="feature-icon" viewBox="0 0 74 66" aria-hidden="true">
      <rect x="0" y="14" width="18" height="40" fill="var(--green)"/>
      <rect x="28" y="32" width="18" height="22" fill="var(--green)"/>
      <rect x="55" y="0" width="18" height="54" fill="var(--green)"/>
      <rect x="0" y="59" width="73" height="5" fill="var(--green)"/>
    </svg>
    <h2 class="feature-title">Progress to Trial</h2>
    <p class="feature-text">Lorem ipsum dolor sit amet, consectetuer adipiscing elit, sed diam nonummy nibh euismod tincidunt ut laoreet dolore magna aliquam erat volutpat. Ut wisi enim ad minim veniam, quis nostrud.</p>
  </section>

  <section class="feature" style="left:609px;top:664px">
    <svg class="feature-icon" viewBox="0 0 74 66" aria-hidden="true">
      <path d="M44 4 H14 a10 10 0 0 0 -10 10 V52 a10 10 0 0 0 10 10 H56 a10 10 0 0 0 10 -10 V30" fill="none" stroke="var(--green)" stroke-width="7"/>
      <path d="M22 48 L25 36 L55 6 L64 15 L34 45 Z" fill="var(--green)"/>
    </svg>
    <h2 class="feature-title">Assess Trial Results</h2>
    <p class="feature-text">Adipiscing elit, sed diam nonummy nibh euismod tincidunt ut laoreet dolore magna aliquam erat volutpat. Ut wisi enim ad minim veniam, quis nostrud exerci tation ullamcorper .</p>
  </section>

  <section class="feature" style="left:62px;top:788px">
    <svg class="feature-icon" viewBox="0 0 74 66" aria-hidden="true">
      <path d="M0 4 H44 L54 4 L72 22 V46 H0 Z" fill="var(--green)"/>
      <path d="M46 10 H52 L62 22 H46 Z" fill="var(--white)"/>
      <circle cx="14" cy="48" r="7" fill="var(--green)" stroke="var(--white)" stroke-width="3"/>
      <circle cx="58" cy="48" r="7" fill="var(--green)" stroke="var(--white)" stroke-width="3"/>
    </svg>
    <h2 class="feature-title">Rollout to balance of Fleet</h2>
    <p class="feature-text">Diam nonummy nibh euismod tincidunt ut laoreet dolore magna aliquam erat volutpat. Ut wisi enim ad minim veniam, quis nostrud exerci tation ullamcorper suscipit lobortis nisl ut aliquip ex.</p>
  </section>

  <section class="feature" style="left:609px;top:788px">
    <svg class="feature-icon" viewBox="0 0 74 66" aria-hidden="true">
      <rect x="2" y="2" width="68" height="64" fill="var(--green)"/>
      <rect x="9" y="14" width="54" height="44" fill="var(--white)"/>
      <rect x="8" y="6" width="4" height="4" fill="var(--white)"/>
      <rect x="15" y="6" width="4" height="4" fill="var(--white)"/>
      <rect x="22" y="6" width="4" height="4" fill="var(--white)"/>
      <polyline points="13,44 22,34 30,44 40,30 48,42 60,34" fill="none" stroke="var(--green)" stroke-width="5"/>
    </svg>
    <h2 class="feature-title">Monitor ongoing cost savings</h2>
    <p class="feature-text">Lorem ipsum dolor sit amet, consectetuer adipiscing elit, sed diam nonummy nibh euismod tincidunt ut laoreet dolore magna aliquam erat volutpat. Ut wisi enim ad minim veniam,.</p>
  </section>

  <footer class="site-footer">
    <div class="social-list">
      <a class="social-link" href="#" style="left:412px">Chatter</a>
      <a class="social-link" href="#" style="left:476px">Friendly</a>
      <a class="social-link" href="#" style="left:540px">Circle</a>
      <a class="social-link" href="#" style="left:604px">Boards</a>
      <a class="social-link" href="#" style="left:669px">Network</a>
    </div>
    <nav class="footer-nav">
      <a href="#">Home</a> · <a href="#">About Us</a> · <a href="#">Products</a> · <a href="#">Features</a> · <a href="#">Options</a> · <a href="#">Replacement Parts</a> · <a href="#">FAQ's</a> · <a href="#">Library</a> · <a href="#">Videos</a> · <a href="#">Contact Us</a>
    </nav>
    <p class="copyright">© Copyright 2002 - 2013 Company Name. All Rights Reserved</p>
  </footer>
</body>
</html>
```